Corporate Business Card

Very professional, Modern, Not to busy, include phone address email, website
(253) 617-4930, 18761 52nd Avenue S, Kent, WA 98047, martin@plumlinegroup.com, varkoworks.com

Target Market(s)

Manufacturing

Industry/Entity Type

Aero, machining, manufacturing, Off road racing

Contact Information for Business Card

Phone, address email, website

```html
<!DOCTYPE html>
<html lang="en">
<head>
<meta charset="utf-8">
<title>Varko Works — Business Card</title>
<link rel="stylesheet" href="https://fonts.googleapis.com/css2?family=Source+Sans+3:wght@400;700&display=swap">
<style>
  :root {
    --backdrop: #979898;
    --card-white: #ffffff;
    --card-dark: #2a2a2c;
    --card-dark-band: #313133;
    --navy: #16346f;
    --red: #d9262c;
    --ink: #555658;
    --white: #ffffff;
  }
  * { box-sizing: border-box; margin: 0; padding: 0; }
  html, body { width: 1200px; height: 1200px; overflow: hidden; }
  body {
    background: var(--backdrop);
    font-family: "Source Sans 3", sans-serif;
    position: relative;
  }
  .card {
    position: absolute;
    left: 231px;
    width: 736px;
    height: 451px;
    overflow: hidden;
  }
  .card-front { top: 116px; background: var(--card-white); }
  .card-back { top: 631px; background: var(--card-dark); }

  .brand {
    position: absolute;
    display: flex;
    align-items: center;
    gap: 14px;
    font-weight: 700;
    letter-spacing: 1px;
    line-height: 1;
    white-space: nowrap;
  }
  .brand-mark { width: 16px; height: 16px; background: var(--red); }
  .brand-front { left: 45px; top: 66px; font-size: 62px; color: var(--navy); }
  .brand-back {
    left: 0; right: 0; top: 192px; justify-content: center;
    font-size: 70px; color: var(--white);
  }

  .person {
    position: absolute;
    right: 45px;
    top: 222px;
    text-align: right;
  }
  .person-name { font-size: 35px; color: var(--red); line-height: 1.1; }
  .person-title { font-size: 23px; color: var(--navy); line-height: 1.2; }

  .divider {
    position: absolute;
    left: 45px; right: 45px; top: 299px;
    height: 2px; background: var(--navy);
  }

  .contact-list {
    position: absolute;
    left: 45px; top: 326px;
    list-style: none;
  }
  .contact-item {
    display: flex; align-items: center;
    height: 30.5px;
    font-size: 19.5px; color: var(--ink);
  }
  .contact-item svg { width: 20px; height: 20px; margin-right: 14px; flex: none; }

  .address {
    position: absolute;
    right: 45px; top: 334px;
    text-align: right;
    font-size: 19.5px; color: var(--ink); line-height: 26.5px;
  }
  .address svg { display: block; margin-left: auto; width: 16px; height: 22px; margin-bottom: 2px; }

  .back-band {
    position: absolute;
    left: 0; right: 0;
    background: var(--card-dark-band);
  }
  .band-top { top: 40px; height: 93px; opacity: .6; }
  .band-low { top: 258px; height: 55px; opacity: .5; }
</style>
</head>
<body>
  <section class="card card-front" aria-label="Business card front">
    <div class="brand brand-front"><span class="brand-mark"></span>VARKO WORKS</div>

    <div class="person">
      <p class="person-name">DANIEL REYES</p>
      <p class="person-title">President</p>
    </div>

    <div class="divider"></div>

    <ul class="contact-list">
      <li class="contact-item">
        <svg viewBox="0 0 24 24" aria-hidden="true"><path fill="#16346f" d="M6.6 2.5l3 3.4c.5.6.5 1.4 0 2L8 9.6c1.2 2.5 3.6 5 6.3 6.4l1.7-1.6c.6-.5 1.4-.5 2 0l3.4 3c.6.5.6 1.4 0 2l-1.8 1.9c-.8.8-2 1-3 .6C9.6 19.4 4.6 14.4 2.1 7.4c-.4-1 0-2.2.7-3l1.8-1.8c.6-.6 1.5-.6 2 0z"/></svg>
        (253) 617-4930
      </li>
      <li class="contact-item">
        <svg viewBox="0 0 24 24" aria-hidden="true"><rect x="1" y="4" width="20" height="14" fill="#16346f"/><path d="M1.5 4.8L11 12l9.5-7.2" fill="none" stroke="#fff" stroke-width="1.6"/><circle cx="19" cy="18" r="4.5" fill="#16346f" stroke="#fff" stroke-width="1.2"/><path d="M17 18l1.5 1.5 2.5-3" fill="none" stroke="#fff" stroke-width="1.4"/></svg>
        martin@plumlinegroup.com
      </li>
      <li class="contact-item">
        <svg viewBox="0 0 24 24" aria-hidden="true"><g fill="none" stroke="#16346f" stroke-width="1.6"><circle cx="12" cy="12" r="10"/><ellipse cx="12" cy="12" rx="4.5" ry="10"/><path d="M2 12h20M4 6.5h16M4 17.5h16"/></g></svg>
        varkoworks.com
      </li>
    </ul>

    <div class="address">
      <svg viewBox="0 0 16 22" aria-hidden="true"><path fill="#16346f" d="M8 0a8 8 0 0 0-8 8c0 5.5 8 14 8 14s8-8.5 8-14a8 8 0 0 0-8-8zm0 11a3 3 0 1 1 0-6 3 3 0 0 1 0 6z"/></svg>
      18761 52nd Avenue S,<br>Kent, WA 98047
    </div>
  </section>

  <section class="card card-back" aria-label="Business card back">
    <div class="back-band band-top"></div>
    <div class="back-band band-low"></div>
    <div class="brand brand-back"><span class="brand-mark"></span>VARKO WORKS</div>
  </section>
</body>
</html>
```